Tall Fern Roofing Business Card

Need a business card with the logo that was designed here

Contact Information for Business Card

Name, Title, Phone, Email, Website, Company name

```html
<!DOCTYPE html>
<html lang="en">
<head>
<meta charset="utf-8">
<title>Tall Fern Roofing Business Card</title>
<link rel="stylesheet" href="https://fonts.googleapis.com/css2?family=Montserrat:wght@400;500;700&display=swap">
<style>
  :root {
    --brand-blue: #3f73b8;
    --paper: #ffffff;
    --backdrop: #c9c9c9;
    --shadow: rgba(0,0,0,0.28);
  }
  * { margin: 0; padding: 0; box-sizing: border-box; }
  html, body { width: 1200px; height: 802px; overflow: hidden; }
  body {
    background: var(--backdrop);
    font-family: "Montserrat", sans-serif;
    position: relative;
  }
  .card {
    position: absolute;
    top: 251px;
    width: 520px;
    height: 300px;
    border-radius: 24px;
    overflow: hidden;
    box-shadow: 0 14px 30px var(--shadow);
  }
  .card--front { left: 50px; background: var(--paper); }
  .card--back { left: 630px; background: var(--brand-blue); }

  .front-band { position: absolute; inset: 0; width: 520px; height: 300px; }

  .wordmark {
    position: absolute;
    font-weight: 700;
    letter-spacing: 0.5px;
    display: flex;
    align-items: center;
    gap: 8px;
    white-space: nowrap;
  }
  .wordmark__square { width: 10px; height: 10px; background: currentColor; }
  .card--front .wordmark { left: 30px; top: 26px; font-size: 18px; color: var(--brand-blue); }
  .card--back .wordmark {
    left: 0; right: 0; top: 130px;
    justify-content: center;
    font-size: 34px; color: var(--paper);
  }
  .card--back .wordmark__square { width: 16px; height: 16px; }

  .person {
    position: absolute;
    left: 30px; bottom: 22px;
    color: var(--paper);
  }
  .person__name { font-size: 17px; font-weight: 700; letter-spacing: 1px; line-height: 22px; }
  .person__title { font-size: 11px; font-weight: 400; line-height: 16px; margin-bottom: 10px; }
  .contact-list { list-style: none; font-size: 12px; line-height: 20px; }
  .contact-list li { display: flex; align-items: center; gap: 8px; }
  .contact-list svg { width: 11px; height: 11px; fill: var(--paper); }

  .address {
    position: absolute;
    right: 28px; top: 118px;
    text-align: right;
    color: var(--paper);
    font-size: 12px;
    font-style: normal;
    line-height: 20px;
  }
</style>
</head>
<body>
  <section class="card card--front" aria-label="Business card front">
    <svg class="front-band" viewBox="0 0 520 300" aria-hidden="true">
      <polygon points="0,150 520,22 520,300 0,300" fill="var(--brand-blue)"/>
      <line x1="0" y1="139" x2="520" y2="11" stroke="var(--brand-blue)" stroke-width="4"/>
    </svg>
    <div class="wordmark"><span class="wordmark__square"></span>Tall Fern Roofing</div>
    <div class="person">
      <p class="person__name">MARCUS HALE</p>
      <p class="person__title">Managing Director</p>
      <ul class="contact-list">
        <li><svg viewBox="0 0 12 12"><path d="M2 1h3l1 3-1.5 1a7 7 0 0 0 2.5 2.5L8 6l3 1v3a1 1 0 0 1-1 1A9 9 0 0 1 1 2a1 1 0 0 1 1-1z"/></svg>0491 555 017</li>
        <li><svg viewBox="0 0 12 12"><path d="M1 2h10v8H1zM1.5 2.5 6 6.5l4.5-4" stroke="#3f73b8" stroke-width="1"/></svg>info@tallfernroofing.com</li>
        <li><svg viewBox="0 0 12 12"><circle cx="6" cy="6" r="5"/></svg>www.tallfernroofing.com</li>
      </ul>
    </div>
    <address class="address">
      1480 W Harbor Road<br>Redvale County Name 4127
    </address>
  </section>

  <section class="card card--back" aria-label="Business card back">
    <div class="wordmark"><span class="wordmark__square"></span>Tall Fern Roofing</div>
  </section>
</body>
</html>
```